Healthy Meal Delivery Website needs a new face lift

Hi there,

The current website i have is super old and outdated.

I would like a beautiful modern site that has all the same content as the previous except with a a new, modern and trustworthy feel.

The current website is http://www.larkibite.ca/

Target Market(s)

Diet Meal delivery, weight loss, healthy meal delivery

Industry/Entity Type

Food Service

Number of Pages Required

5+ page

Font styles to use
Sans Serif

Requirements
Must have
• Modern & Clean
Should not have
• Anything outdated or cheesy

```html
<!DOCTYPE html>
<html lang="en">
<head>
<meta charset="utf-8">
<title>Lark Bite Delivery – Fresh Diet Meals Delivered</title>
<link href="https://fonts.googleapis.com/css2?family=Montserrat:wght@400;500;600;700&family=Open+Sans:ital,wght@0,400;0,600;1,400&display=swap" rel="stylesheet">
<style>
:root{
  --blue:#29b6e5;
  --blue-dark:#0f8fbf;
  --ink:#333a40;
  --muted:#555c62;
  --pale:#e3f3fa;
  --night:#070808;
  --white:#ffffff;
  --star:#f5b400;
}
*{box-sizing:border-box;margin:0;padding:0}
html,body{width:1200px;height:3509px;overflow:hidden}
body{position:relative;background:var(--white);font-family:'Open Sans',sans-serif;color:var(--ink)}
.abs{position:absolute}
/* header */
.topbar{left:450px;top:0;width:750px;height:36px;background:var(--blue);clip-path:polygon(20px 0,100% 0,100% 100%,0 100%);color:#fff;font-size:13px;display:flex;align-items:center;padding-left:60px;gap:14px;white-space:nowrap}
.topbar .sq{width:11px;height:11px;background:#fff;border-radius:2px;display:inline-block}
.brand{left:86px;top:30px;font-family:'Montserrat',sans-serif;font-weight:700;font-size:34px;color:var(--blue);display:flex;align-items:center;gap:10px}
.brand .dot{width:22px;height:22px;border-radius:50%;background:var(--blue)}
.nav{left:354px;top:66px;display:flex;gap:16px;font-family:'Montserrat',sans-serif;font-size:12.5px;font-weight:500;color:var(--ink);align-items:center;white-space:nowrap}
.nav .login{background:var(--blue);color:#fff;border-radius:16px;padding:6px 14px}
/* hero */
.hero-photo{left:0;top:124px;width:1200px;height:620px;background:radial-gradient(ellipse at 55% 40%,#e8e2d6 0%,#b9a58a 25%,#5a4632 50%,#1c1611 80%)}
.hero-title{left:86px;top:280px;font-family:'Montserrat',sans-serif;font-size:40px;font-weight:500;color:#fff}
.hero-sub{left:90px;top:338px;font-size:18px;color:#fff}
.hero-btn{left:88px;top:385px;width:140px;height:42px;background:var(--blue);color:#fff;font-family:'Montserrat',sans-serif;font-size:13px;font-weight:600;display:flex;align-items:center;justify-content:center}
.dots{left:93px;top:452px;display:flex;gap:5px}
.dots i{width:13px;height:13px;border:2px solid #fff;border-radius:50%}
.dots i.on{background:var(--blue);border-color:var(--blue)}
/* intro */
.h2{font-family:'Montserrat',sans-serif;font-weight:600;color:var(--blue);font-size:29px;text-align:center;width:1200px;left:0;letter-spacing:.5px}
.by{left:0;width:1200px;top:774px;text-align:center;font-family:'Montserrat',sans-serif;font-size:29px;font-weight:600;color:var(--ink)}
.intro{left:160px;width:880px;top:838px;text-align:center;font-size:17px;line-height:29px;color:var(--muted)}
.feature{width:320px;display:flex;gap:16px}
.feature .ic{width:70px;height:70px;border-radius:50%;background:var(--blue);flex:none;display:flex;align-items:center;justify-content:center;box-shadow:0 0 0 4px #c9ecf8}
.feature h3{font-family:'Montserrat',sans-serif;font-size:16px;font-weight:600;margin-top:10px;letter-spacing:.5px}
.feature p{font-size:13px;line-height:21px;color:var(--muted);margin-top:4px}
/* program */
.program{left:0;top:1306px;width:1200px;height:612px;background:var(--pale)}
.card{top:1480px;height:328px;border:4px solid #fff;box-shadow:0 2px 6px rgba(0,0,0,.12)}
.card .cap{position:absolute;left:16px;bottom:22px;color:#fff;font-family:'Montserrat',sans-serif}
.card .cap b{display:block;font-size:17px;font-weight:600;letter-spacing:1px;line-height:27px}
.card .cap span{display:block;font-size:13px;margin-top:18px}
.card .cap p{font-family:'Open Sans',sans-serif;font-size:12px;line-height:21px;margin-top:10px;width:280px}
.arrow{width:28px;height:28px;border-radius:50%;background:#2b2f33;display:flex;align-items:center;justify-content:center}
.arrow.light{background:#c9cbcd}
/* testimonials */
.tcard{top:2120px;height:196px;border:2px solid #d6d6d6;background:#fff}
.tcard.active{border-color:var(--blue)}
.tcard .q{position:absolute;left:0;top:-2px;width:52px;height:50px;background:#222;clip-path:polygon(0 0,100% 50%,0 100%)}
.tcard.active .q{background:var(--blue)}
.tcard h4{position:absolute;left:16px;top:60px;font-family:'Montserrat',sans-serif;font-size:14px;font-weight:600}
.tcard .txt{position:absolute;left:16px;top:85px;width:300px;font-size:12px;line-height:19px;font-style:italic;color:#333}
.tcard .av{position:absolute;left:36px;top:148px;width:66px;height:66px;border-radius:50%;border:3px solid #ddd;background:linear-gradient(#c9a98a,#8a6a52)}
.tcard .who{position:absolute;left:130px;top:150px;font-size:13px;color:var(--blue)}
.tcard .who small{color:#333;font-size:11px}
.tcard .stars{position:absolute;left:130px;top:170px;color:var(--star);font-size:15px;letter-spacing:2px}
/* banner */
.banner{left:85px;top:2421px;width:1028px;height:216px;background:linear-gradient(var(--blue),var(--blue-dark));box-shadow:0 6px 14px rgba(0,0,0,.25);color:#fff}
.banner .ask{position:absolute;right:676px;top:58px;text-align:right;font-family:'Montserrat',sans-serif;font-size:31px;line-height:45px;white-space:nowrap}
.banner .rule{position:absolute;left:383px;top:38px;width:3px;height:140px;background:#fff}
.banner .c{position:absolute;left:410px;top:48px;font-family:'Montserrat',sans-serif;white-space:nowrap}
.banner .c h5{font-size:28px;font-weight:500}
.banner .c p{font-size:20px;margin-top:16px;display:flex;gap:14px;align-items:center}
/* footer */
.footer{left:0;top:2780px;width:1200px;height:729px;background:var(--night);color:#fff}
.light-text{color:#fff}
.vert{left:95px;top:3360px;transform:rotate(-90deg);transform-origin:0 0;font-family:'Montserrat',sans-serif;font-weight:700;color:var(--blue);font-size:24px;line-height:44px;width:450px}
.addr{left:260px;top:3020px;font-size:14px;line-height:29px;color:#fff}
.addr .lbl{color:var(--blue);font-weight:600}
.addr .row{display:flex;gap:14px}
.social{left:290px;top:3300px;display:flex;gap:12px}
.social i{width:10px;height:10px;border-radius:50%;background:#fff}
.vline{left:600px;top:2990px;width:1px;height:390px;background:#555}
.field{width:200px;border-bottom:1px solid #888;font-size:12px;font-weight:600;height:38px;color:#fff}
.msg{left:680px;top:3140px;width:430px;color:#fff}
.msg .box{margin-top:10px;height:82px;border:1px solid #888}
.send{left:678px;top:3275px;width:202px;height:40px;border-radius:20px;background:#fff;color:var(--blue);font-family:'Montserrat',sans-serif;font-size:16px;letter-spacing:1px;display:flex;align-items:center;justify-content:center}
.hline{left:85px;top:3390px;width:1030px;height:1px;background:#444}
.copy{left:88px;top:3440px;font-size:12px;letter-spacing:.5px;color:#fff}
.fnav{left:660px;top:3440px;font-size:12px;display:flex;gap:10px;color:#fff}
</style>
</head>
<body>

<header>
  <div class="abs topbar">
    <span>&#9990; Contact Us: 416-555-0148</span><span>|</span>
    <span>&#9993; Mail To: hello@larkbitedelivery.ca</span><span>|</span>
    <span class="sq"></span><span class="sq"></span><span class="sq"></span><span class="sq"></span><span class="sq"></span>
  </div>
  <div class="abs brand"><span class="dot"></span>Lark Bite</div>
  <nav class="abs nav">
    <span>Home</span><span>How It Works</span><span>Pricing</span><span>Sample Menu</span><span>Celebrity</span><span>F.A.Q.</span><span>Contact</span><span>Sign Up</span><span class="login">Customer Login</span>
  </nav>
</header>

<section class="hero">
  <div class="abs hero-photo" role="img" aria-label="Plated grilled fish with lentils and vegetables"></div>
  <svg class="abs" style="left:0;top:560px" width="1200" height="200" viewBox="0 0 1200 200">
    <path d="M0 130 Q600 140 1200 10 L1200 200 L0 200Z" fill="#fff"/>
    <path d="M560 120 Q900 100 1200 0 L1200 220 Q1100 120 900 125 Q700 130 560 120Z" fill="#29b6e5"/>
    <path d="M0 132 Q600 150 1200 60 L1200 200 L0 200Z" fill="#fff"/>
  </svg>
  <h1 class="abs hero-title">Fresh diet meals delivered</h1>
  <p class="abs hero-sub">Providing Toronto diet meal delivery for 15 years.</p>
  <div class="abs hero-btn">READ MORE &gt;</div>
  <div class="abs dots"><i></i><i></i><i class="on"></i><i></i><i></i></div>
</section>

<section class="intro-section">
  <h2 class="abs h2" style="top:722px">FRESH DIET GOURMET MEALS DELIVERED</h2>
  <p class="abs by">by Lark Bite</p>
  <p class="abs intro">Fresh diet meal delivery Toronto and Canada wide is our signature fresh gourmet diet meal delivery program designed for healthy living &amp; weight loss management. Diet meal delivery Toronto has a creative gourmet menu that uses exotic flavors and ingredients to enhance your dining experience.</p>

  <div class="abs feature" style="left:110px;top:985px">
    <div class="ic"><svg width="34" height="34" viewBox="0 0 24 24"><path d="M2 10h4v11H2zM8 21h9l3-8v-3h-6l1-5-2-2-5 6z" fill="#fff"/></svg></div>
    <div><h3>BENEFITS</h3><p>Fresh diet meal delivery daily</p></div>
  </div>
  <div class="abs feature" style="left:455px;top:985px">
    <div class="ic"><svg width="34" height="34" viewBox="0 0 24 24"><rect x="5" y="3" width="14" height="18" rx="1" fill="none" stroke="#fff" stroke-width="2"/><path d="M8 8h8M8 12h8M8 16h5" stroke="#fff" stroke-width="2"/></svg></div>
    <div><h3>MENU</h3><p>Inspired fresh<br>gourmet Lark Diet meals</p></div>
  </div>
  <div class="abs feature" style="left:800px;top:985px">
    <div class="ic"><svg width="36" height="36" viewBox="0 0 24 24"><path d="M3 17a9 9 0 0 1 18 0z" fill="#fff"/><rect x="2" y="18" width="20" height="2" fill="#fff"/><circle cx="12" cy="6" r="1.5" fill="#fff"/></svg></div>
    <div><h3>VARIETY</h3><p>60 Day Menu Rotation</p></div>
  </div>
  <div class="abs feature" style="left:110px;top:1128px">
    <div class="ic"><svg width="34" height="34" viewBox="0 0 24 24"><circle cx="8" cy="8" r="4" fill="none" stroke="#fff" stroke-width="2"/><circle cx="16" cy="8" r="4" fill="none" stroke="#fff" stroke-width="2"/><path d="M6 14h10l2 8H8z" fill="#fff"/></svg></div>
    <div><h3>CUSTOMIZATION</h3><p>Every fresh Lark Diet<br>meal is personally customized</p></div>
  </div>
  <div class="abs feature" style="left:455px;top:1128px">
    <div class="ic"><svg width="38" height="34" viewBox="0 0 26 24"><rect x="2" y="6" width="14" height="11" fill="#fff"/><path d="M16 9h5l3 4v4h-8z" fill="#fff"/><circle cx="7" cy="19" r="2.5" fill="#fff"/><circle cx="20" cy="19" r="2.5" fill="#fff"/></svg></div>
    <div><h3>DELIVERY</h3><p>Fresh diet meal delivery<br>daily Toronto and Canada wide</p></div>
  </div>
  <div class="abs feature" style="left:800px;top:1128px">
    <div class="ic"><svg width="36" height="36" viewBox="0 0 24 24"><circle cx="12" cy="12" r="9" fill="none" stroke="#fff" stroke-width="2"/><text x="12" y="15.5" text-anchor="middle" font-family="Montserrat,sans-serif" font-size="9" font-weight="700" fill="#fff">24</text></svg></div>
    <div><h3>CUSTOMER SERVICE</h3><p>Personal Nutritionist<br>available 7 days a week</p></div>
  </div>
</section>

<section>
  <div class="abs program"></div>
  <h2 class="abs h2" style="top:1407px">PROGRAM DETAILS</h2>
  <div class="abs arrow" style="left:30px;top:1630px"><svg width="12" height="12" viewBox="0 0 12 12"><path d="M8 1L3 6l5 5" stroke="#fff" stroke-width="2.5" fill="none"/></svg></div>
  <div class="abs arrow" style="left:1140px;top:1630px"><svg width="12" height="12" viewBox="0 0 12 12"><path d="M4 1l5 5-5 5" stroke="#fff" stroke-width="2.5" fill="none"/></svg></div>

  <div class="abs card" style="left:90px;width:325px">
    <div style="position:absolute;inset:0;background:linear-gradient(160deg,#e8d7b8,#b88a55 45%,#5a3d25)" role="img" aria-label="Fresh wrap with grilled vegetables"></div>
    <div class="cap"><b>PAUSE YOUR<br>PROGRAM ANYTIME</b><span>Order Now &gt;</span></div>
  </div>
  <div class="abs card" style="left:440px;width:320px">
    <div style="position:absolute;inset:0;background:linear-gradient(160deg,#5c3a2a,#2e1c15 60%,#1a100c)" role="img" aria-label="Gourmet plated dish"></div>
    <div class="cap" style="bottom:28px"><b style="color:var(--blue)">ENJOY OUR<br>GOURMET MENU</b><p>Every fresh diet meal delivered is prepared with the finest ingredients available and has a creative menu that uses unique and exotic flavors and ingredients to enhance your dining experience.</p><span style="color:var(--blue);margin-top:14px">Order Now &gt;</span></div>
  </div>
  <div class="abs card" style="left:787px;width:323px">
    <div style="position:absolute;inset:0;background:linear-gradient(160deg,#f2efea,#c9bfb3 50%,#7d6a5c)" role="img" aria-label="Smiling woman enjoying a meal"></div>
    <div class="cap"><b>CUSTOMIZED<br>FOR YOU</b><span>Order Now &gt;</span></div>
  </div>
</section>

<section>
  <h2 class="abs h2" style="top:2035px">CELEBRITY TESTIMONIALS</h2>
  <div class="abs arrow light" style="left:26px;top:2218px"><svg width="12" height="12" viewBox="0 0 12 12"><path d="M8 1L3 6l5 5" stroke="#fff" stroke-width="2.5" fill="none"/></svg></div>
  <div class="abs arrow light" style="left:1146px;top:2218px"><svg width="12" height="12" viewBox="0 0 12 12"><path d="M4 1l5 5-5 5" stroke="#fff" stroke-width="2.5" fill="none"/></svg></div>

  <article class="abs tcard" style="left:90px;width:315px">
    <div class="q"></div><h4>Tasty &amp; Healthy</h4>
    <p class="txt">"The Lark Diet is simple and it works! I am so greatful to have used the Lark Diet. So tasty and so healthy."</p>
    <div class="av" role="img" aria-label="Portrait of Claire Holloway"></div>
    <p class="who">Claire Holloway, <small>Actress</small></p><p class="stars">★★★★★</p>
  </article>
  <article class="abs tcard active" style="left:433px;width:332px">
    <div class="q"></div><h4>Fresh &amp; Delicious</h4>
    <p class="txt">"When in Toronto filming I know I can depend on Larkibite.ca for fresh, delicious meals delivered daily, fabulous, easy and convenient."</p>
    <div class="av" role="img" aria-label="Portrait of Marcus Reid"></div>
    <p class="who">Marcus Reid, <small>Actress</small></p><p class="stars">★★★★★</p>
  </article>
  <article class="abs tcard" style="left:778px;width:332px">
    <div class="q"></div><h4>Hectic Schedule</h4>
    <p class="txt">"I never used a prepared food service before but with my schedule on set Lark Bite has been a blessing to me."</p>
    <div class="av" role="img" aria-label="Portrait of Dana Whitfield"></div>
    <p class="who">Dana Whitfield, <small>Actress</small></p><p class="stars">★★★★★</p>
  </article>
</section>

<section class="abs banner">
  <p class="ask">Still have<br>Questions?</p>
  <div class="rule"></div>
  <div class="c">
    <h5>Contact Us now at:</h5>
    <p><svg width="18" height="18" viewBox="0 0 24 24"><path d="M6 2l4 4-2 3a12 12 0 0 0 7 7l3-2 4 4-3 4C10 22 2 14 2 5z" fill="#fff"/></svg>TEL: 416-555-0148</p>
    <p style="margin-top:12px"><svg width="18" height="18" viewBox="0 0 24 24"><rect x="2" y="5" width="20" height="14" fill="#fff"/><path d="M2 5l10 8 10-8" stroke="#0f8fbf" stroke-width="2" fill="none"/></svg>EMAIL: hello@larkbitedelivery.ca</p>
  </div>
</section>

<footer>
  <svg class="abs" style="left:0;top:2690px" width="1200" height="100" viewBox="0 0 1200 100" preserveAspectRatio="none">
    <path d="M0 0 Q300 110 1200 30 L1200 100 L0 100Z" fill="#29b6e5"/>
    <path d="M0 40 Q300 120 1200 30 L1200 100 L0 100Z" fill="#070808"/>
  </svg>
  <div class="abs footer"></div>
  <p class="abs vert">Get In Touch - Diet Meal Delivery<br>Toronto Or Canada Wide</p>
  <div class="abs addr">
    <div class="row"><span class="lbl">&#9679;</span><div><span class="lbl">Canada</span><br>418 Maple Grove Ave<br>Toronto, ON, M4T 2J5</div></div>
    <div class="row" style="margin-top:14px"><span>&#9990;</span><div>Call: +416-555-0148</div></div>
    <div class="row" style="margin-top:14px"><span class="lbl">&#9679;</span><div><span class="lbl">United States</span><br>1450 Cedar Ridge Road, Suite 210<br>Birmingham, Alabama, 35216</div></div>
  </div>
  <div class="abs social"><i></i><i></i><i></i><i></i><i></i><i></i></div>
  <div class="abs vline"></div>
  <form>
    <div class="abs field" style="left:680px;top:3020px">First Name</div>
    <div class="abs field" style="left:910px;top:3020px">Sur Name</div>
    <div class="abs field" style="left:680px;top:3080px">Phone</div>
    <div class="abs field" style="left:910px;top:3080px">Email</div>
    <div class="abs msg"><span style="font-size:12px;font-weight:600">Message</span><div class="box"></div></div>
    <div class="abs send">SEND</div>
  </form>
  <div class="abs hline"></div>
  <p class="abs copy">© COPYRIGHT 2018. Lark Bite Meals. ALL RIGHTS RESERVED.</p>
  <p class="abs fnav"><span>Home</span>|<span>How It Works</span>|<span>Pricing</span>|<span>Sign Up</span>|<span>Contact Us</span>|<span>Terms Of Use</span></p>
</footer>

</body>
</html>
```